Help our Sugar Loom find our winning design! We're looking for a business card....

We’re a Sugar Loom in NY specializing in custom-made cakes and unique desserts.
Our cakes combine flavor and art, each designed to match customer’s special event and theme.
We’d like a unique business card with a clean design that will combine French chic and artistic look & feel.
We’d like to differentiate ourselves from standard bakeries, please don’t offer cupcake images :-)
Our logo is peach-pink and brown and we’d love to use these colors ( . Another color that can be added is gold - or feel free to suggest!

Target Market(s)

Women, ages 25-55

Industry/Entity Type

Boutique

Contact Information for Business Card

Text on card:
Logo
Sugar Loom by Dana Welch

www.sugarloomsweets.com
hello@sugarloom.com
(516) 555-0147
F – sugarloomnyc
IG - sugarloom_ny

Font styles to use
Sans Serif
Script

Requirements
Must have
• Logo
• Clean look
• French chic and artistic look & feel.
Nice to have
• Damask pattern
Should not have
• Cupcake images

```html
<!DOCTYPE html>
<html lang="en">
<head>
<meta charset="utf-8">
<title>Sugar Loom – Business Card</title>
<link rel="stylesheet" href="https://fonts.googleapis.com/css2?family=Open+Sans:wght@400;600&family=Pinyon+Script&display=swap">
<style>
  :root {
    --backdrop: #e4e4e4;
    --card-pink: #dea3ab;
    --card-pink-soft: #e8b6bc;
    --band-magenta: #d9177f;
    --panel-white: #ffffff;
    --peach-line: #ee9c8c;
    --brown: #3b2a26;
    --ink: #141414;
    --text-light: #fff4f5;
  }
  * { margin: 0; padding: 0; box-sizing: border-box; }
  html, body { width: 1200px; height: 852px; overflow: hidden; }
  body {
    background: var(--backdrop);
    font-family: "Open Sans", Arial, sans-serif;
    position: relative;
  }
  .card {
    position: absolute;
    width: 520px;
    height: 300px;
    border-radius: 22px;
    overflow: hidden;
    box-shadow: 0 6px 16px rgba(0,0,0,0.18);
  }
  .card-front { left: 80px; top: 110px; }
  .card-back { left: 600px; top: 442px; }
  .card-texture {
    position: absolute; inset: 0;
    background: linear-gradient(135deg, var(--card-pink-soft), var(--card-pink) 60%);
  }
  .ribbon-band {
    position: absolute; left: 0; right: 0; top: 128px; height: 46px;
    background: var(--band-magenta);
    border-top: 2px solid rgba(255,255,255,0.5);
    border-bottom: 2px solid rgba(255,255,255,0.5);
  }
  .logo-panel {
    position: absolute;
    background: var(--panel-white);
    border: 2px solid var(--peach-line);
    border-radius: 60px;
    display: flex; align-items: center; justify-content: center;
    box-shadow: 0 2px 6px rgba(0,0,0,0.15);
  }
  .card-front .logo-panel { left: 110px; top: 78px; width: 300px; height: 146px; }
  .card-back .logo-panel { left: 34px; top: 102px; width: 210px; height: 104px; border-radius: 44px; }
  .brand-name {
    font-family: "Open Sans", Arial, sans-serif;
    font-weight: 400;
    color: var(--brown);
    letter-spacing: 1px;
    white-space: nowrap;
  }
  .card-front .brand-name { font-size: 38px; }
  .card-back .brand-name { font-size: 26px; }
  .divider-stroke { position: absolute; left: 250px; top: 28px; }
  .owner-block { position: absolute; left: 300px; top: 32px; color: var(--text-light); }
  .owner-intro { font-size: 15px; }
  .owner-name { font-family: "Pinyon Script", cursive; font-size: 30px; line-height: 1.1; margin-left: 26px; }
  .contact-list {
    position: absolute; left: 300px; top: 132px;
    list-style: none; color: var(--text-light); font-size: 13px;
  }
  .contact-list li { display: flex; align-items: center; gap: 10px; height: 22px; white-space: nowrap; }
  .contact-icon { width: 12px; height: 12px; flex: none; }
</style>
</head>
<body>

  <section class="card card-front">
    <div class="card-texture" role="img" aria-label="Soft pink card background with a faint tone-on-tone damask pattern"></div>
    <div class="ribbon-band"></div>
    <div class="logo-panel">
      <span class="brand-name">Sugar Loom</span>
    </div>
  </section>

  <section class="card card-back">
    <div class="card-texture" role="img" aria-label="Soft pink card background with a faint tone-on-tone damask pattern"></div>
    <div class="logo-panel">
      <span class="brand-name">Sugar Loom</span>
    </div>

    <svg class="divider-stroke" width="12" height="240" viewBox="0 0 12 240" aria-hidden="true">
      <path d="M6 0 Q9 120 6 240 Q3 120 6 0 Z" fill="var(--ink)"/>
    </svg>

    <div class="owner-block">
      <p class="owner-intro">Sugar Loom by</p>
      <p class="owner-name">Dana Welch</p>
    </div>

    <ul class="contact-list">
      <li>
        <svg class="contact-icon" viewBox="0 0 12 12" aria-hidden="true"><path d="M2 1h2.5l1 3-1.5 1a7 7 0 0 0 3 3l1-1.5 3 1V11A9 9 0 0 1 1 2z" fill="var(--ink)"/></svg>
        (516) 555-0147
      </li>
      <li>
        <svg class="contact-icon" viewBox="0 0 12 12" aria-hidden="true"><rect x="0.5" y="2.5" width="11" height="7" fill="var(--ink)"/><path d="M0.5 2.5 6 7l5.5-4.5" stroke="#fff" fill="none"/></svg>
        hello@sugarloom.com
      </li>
      <li>
        <svg class="contact-icon" viewBox="0 0 12 12" aria-hidden="true"><circle cx="6" cy="6" r="5.5" fill="var(--ink)"/><path d="M0.5 6h11M6 0.5c-3 3-3 8 0 11M6 0.5c3 3 3 8 0 11" stroke="#fff" stroke-width="0.8" fill="none"/></svg>
        www.sugarloomsweets.com
      </li>
      <li>
        <svg class="contact-icon" viewBox="0 0 12 12" aria-hidden="true"><rect width="12" height="12" rx="2" fill="var(--ink)"/></svg>
        sugarloomnyc
      </li>
      <li>
        <svg class="contact-icon" viewBox="0 0 12 12" aria-hidden="true"><rect width="12" height="12" rx="2" fill="var(--ink)"/></svg>
        sugarloom_ny
      </li>
    </ul>
  </section>

</body>
</html>
```